Flyer for customer acquisition.

Hello, We are a sportmanagement agency from Germany and we need information flyers for customer acquisition. It should be DinA4 and should have a modern but serious design. I have uploaded a information sheet, where you can find the text and the composition, the flyer should have. I also uploaded Pictures / Images, which you can use. Of course you can use other suitable images. If they are not free, I will buy them later. On the bottom of the flyer there has been the contact information. You will find them in the download section, too. If you have questions, just write me. If I forgot something, I will update the letter :) Thank you very much!
Ich brauche zusätzliche Tage um durchzusehen

```html
<!DOCTYPE html>
<html lang="de">
<head>
<meta charset="utf-8">
<title>VKS Nachwuchsförderung Flyer</title>
<link href="https://fonts.googleapis.com/css2?family=Michroma&family=Orbitron:wght@700;900&family=Open+Sans:wght@400;700&display=swap" rel="stylesheet">
<style>
  :root {
    --page-bg: #d9d9d9;
    --navy-deep: #06121f;
    --navy: #0d2436;
    --navy-mid: #173c57;
    --sky: #3aa3dc;
    --orange: #f28a1c;
    --white: #ffffff;
    --text-soft: #e6edf2;
    --footer: #2b2b2b;
  }
  * { margin: 0; padding: 0; box-sizing: border-box; }
  html, body { width: 707px; height: 1200px; overflow: hidden; background: var(--page-bg); }
  .flyer {
    position: absolute; left: 24px; top: 134px; width: 660px; height: 933px; overflow: hidden;
    background: linear-gradient(180deg, var(--navy-deep) 0%, var(--navy) 45%, var(--navy-mid) 75%, #1f5878 100%);
    font-family: "Open Sans", Arial, sans-serif; color: var(--white);
  }
  .hero-photo {
    position: absolute; left: 0; top: 0; width: 660px; height: 390px;
    background:
      radial-gradient(ellipse at 50% 20%, #9fb8d0 0%, rgba(90,120,150,0.6) 25%, transparent 55%),
      linear-gradient(180deg, #1d3550 0%, #2a4663 40%, #203a4e 62%, #2e5360 75%, var(--navy) 100%);
  }
  .brand {
    position: absolute; top: 340px; left: 0; width: 100%; text-align: center;
    font-family: "Michroma", sans-serif; font-size: 26px; color: var(--white); letter-spacing: 1px;
  }
  .headline { position: absolute; top: 410px; width: 100%; text-align: center; }
  .headline .line-agency { font-family: "Michroma", sans-serif; font-size: 20px; letter-spacing: 0.5px; }
  .headline .line-management { font-family: "Orbitron", sans-serif; font-weight: 900; font-size: 40px; color: var(--sky); margin-top: 2px; letter-spacing: 1px; }
  .tagline { position: absolute; top: 505px; width: 100%; text-align: center; }
  .tagline .line-accent { font-family: "Orbitron", sans-serif; font-weight: 900; font-size: 29px; color: var(--orange); letter-spacing: 1px; }
  .tagline .line-sub { font-family: "Michroma", sans-serif; font-size: 20px; margin-top: 4px; }
  .services {
    position: absolute; top: 598px; left: 28px; width: 604px;
    display: grid; grid-template-columns: repeat(3, 1fr); column-gap: 30px; text-align: center;
  }
  .service { margin-bottom: 12px; }
  .service h3 { font-size: 11px; font-weight: 700; color: var(--orange); text-transform: none; line-height: 1.25; margin-bottom: 8px; }
  .service p { font-size: 10px; line-height: 1.45; color: var(--text-soft); }
  .footnotes {
    position: absolute; top: 843px; left: 30px; width: 600px; text-align: center;
    font-size: 8px; line-height: 1.4; color: var(--text-soft);
  }
  .contact-bar {
    position: absolute; left: 0; bottom: 0; width: 100%; height: 38px; background: var(--footer);
    display: flex; align-items: center; justify-content: center; gap: 18px; font-weight: 700;
  }
  .contact-item { display: flex; align-items: center; gap: 7px; font-size: 14px; }
  .contact-item.phone { font-size: 18px; }
  .divider { width: 1px; height: 20px; background: #777; }
  .icon { width: 13px; height: 13px; }
</style>
</head>
<body>
<main class="flyer">
  <div class="hero-photo" role="img" aria-label="Fußballspieler von hinten mit Ball unter dem Arm im beleuchteten Stadion"></div>

  <div class="brand">VKS</div>

  <h1 class="headline">
    <div class="line-agency">VKS NACHWUCHSFÖRDERUNG</div>
    <div class="line-management">UND -MANGEMENT</div>
  </h1>

  <div class="tagline">
    <div class="line-accent">WIR BEGLEITEN DICH</div>
    <div class="line-sub">AUF DEINEM WEG ZUM PROFI</div>
  </div>

  <section class="services">
    <div class="service">
      <h3>KARRIEREPLANUNG</h3>
      <p>Wir haben deine Karriere im Blick! In enger Absprache mit deinen Eltern und dir leiten wir die richtigen Maßnahmen und Schritte ein, um dein Ziel „Profifußballer“ zu realisieren</p>
    </div>
    <div class="service">
      <h3>STÄNDIGER<br>ANSPRECHPARTNER</h3>
      <p>Egal um welchen Themen es sich handelt, wir sind für dich da! Ein vertrauensvolles und freundschaftliches Verhältnis ist uns besonders wichtig.</p>
    </div>
    <div class="service">
      <h3>Rechtsberatung/<br>Vertragsrecht</h3>
      <p>Juristendeutsch und Kleingedrucktes? Kein Problem! Wir helfen dir den Durchblick zu behalten und holen immer das Beste für dich raus.</p>
    </div>
    <div class="service">
      <h3>AUSRÜSTUNG</h3>
      <p>Wir besorgen dir deine Ausrüstung! Unsere Beziehungen zu den großen Sportartikelherstellern ermöglichen den Abschluss von Ausrüsterverträgen*.</p>
    </div>
    <div class="service">
      <h3>VORSORGE</h3>
      <p>Verletzungen gehören leider zum Fußball dazu.<br>Wir sichern dich ab, indem wir eine private Zusatzkrankenversicherung für dich abschließen.</p>
    </div>
    <div class="service">
      <h3>Kooperationspartner/<br>Netzwerk</h3>
      <p>Ob Entscheidungsträger oder Experte, wir kennen die richtigen Leute. Zusätzlich bieten wir dir eine große Bandbreite an Leistungen, die du jederzeit in Anspruch nehmen kannst**.</p>
    </div>
  </section>

  <div class="footnotes">
    <p>*Die Entscheidung über das Zustandekommen eines Ausrüstervertrags obliegt dem jeweiligen Sportartikelhersteller. Ist ein Abschluss aktuell nicht möglich, erhältst du von uns 2x pro Saison neue Fußballschuhe sowie weitere Ausrüstungsgegenstände.</p>
    <p>**Personal Training, Athletik-Training, Ernährungsberatung, Sportpsychologische Betreuung, usw.</p>
  </div>

  <footer class="contact-bar">
    <div class="contact-item">
      <svg class="icon" viewBox="0 0 16 16"><circle cx="8" cy="8" r="7.5" fill="#bbb"/><rect x="4" y="5.5" width="8" height="5.5" fill="#2b2b2b"/><path d="M4 5.5 L8 8.5 L12 5.5" stroke="#bbb" fill="none"/></svg>
      info@vks-sport.de
    </div>
    <span class="divider"></span>
    <div class="contact-item">
      <svg class="icon" viewBox="0 0 16 16"><circle cx="8" cy="8" r="7" fill="none" stroke="#bbb" stroke-width="1.5"/><ellipse cx="8" cy="8" rx="3" ry="7" fill="none" stroke="#bbb"/><line x1="1" y1="8" x2="15" y2="8" stroke="#bbb"/></svg>
      www.vks-sport.de
    </div>
    <span class="divider"></span>
    <div class="contact-item phone">
      <svg class="icon" viewBox="0 0 16 16"><path d="M4 1.5 L6.5 4.5 L5 6.5 C6 8.5 7.5 10 9.5 11 L11.5 9.5 L14.5 12 L12.5 14.5 C7 14 2 9 1.5 3.5 Z" fill="#ddd"/></svg>
      01234/5678900
    </div>
  </footer>
</main>
</body>
</html>
```